Pepper & Palm Business Card FUN & EXCITING

Here is the Information for the Card:
Jaswinder Bains (Ravi)
E: RaviBains@postlark.com
C: (480) 555-0147
www.PepperPalmLV.com

We don't want traditional Indian cliche, We a playful bold and fun business card.

Files: https://files.cloudvessel.net/share/folders/7TqRmXpZ2vKa9LwBn4YcHd3JsEf6UoGi?usp=share_link

https://files.cloudvessel.net/share/folders/4MzXaQ8rTw2YbNcVk6PsLe5GhJdR3FoU?usp=share_link

Target Market(s)

Las Vegas Local Restaurant

Industry/Entity Type

Indian Restaurant

Contact Information for Business Card

Name, Email, Cell Phone, Company Logo

```html
<!DOCTYPE html>
<html lang="en">
<head>
<meta charset="utf-8">
<title>Pepper &amp; Palm — Business Card</title>
<link rel="stylesheet" href="https://fonts.googleapis.com/css2?family=Montserrat:wght@400;600;800&display=swap">
<style>
  :root {
    --backdrop: #2e2e2e;
    --card: #1f1f1f;
    --ink: #ffffff;
    --accent: #e8792b;
    --muted: #bdbdbd;
    --art-warm: #e9a25b;
    --art-cream: #efe6cc;
  }
  * { margin: 0; padding: 0; box-sizing: border-box; }
  html, body { width: 1200px; height: 1108px; overflow: hidden; }
  body {
    background: var(--backdrop);
    font-family: "Montserrat", sans-serif;
    color: var(--ink);
    position: relative;
  }
  .card {
    position: absolute;
    left: 257px;
    width: 696px;
    background: var(--card);
    border-radius: 18px;
  }
  .card--front { top: 128px; height: 426px; }
  .card--back { top: 594px; height: 440px; }

  .brand-name {
    position: absolute;
    left: 0; right: 0;
    text-align: center;
    font-weight: 800;
    font-size: 56px;
    letter-spacing: -1px;
    line-height: 1;
    color: var(--ink);
  }
  .card--front .brand-name { top: 130px; }
  .card--back .brand-name { top: 100px; }

  .mascot-art {
    position: absolute;
    left: 236px; top: 218px;
    width: 224px; height: 140px;
    border-radius: 14px;
    background: linear-gradient(120deg, var(--art-cream), var(--art-warm));
  }
  .tagline {
    position: absolute;
    left: 0; right: 0; top: 366px;
    text-align: center;
    font-size: 10px;
    color: var(--muted);
    letter-spacing: 0.5px;
  }

  .owner {
    position: absolute;
    right: 343px; top: 280px;
    text-align: right;
  }
  .owner__name {
    font-weight: 600;
    font-size: 26px;
    color: var(--accent);
    line-height: 1.1;
    white-space: nowrap;
  }
  .owner__role { font-size: 15px; color: var(--ink); }

  .divider {
    position: absolute;
    left: 364px; top: 266px;
    width: 2px; height: 84px;
    background: var(--accent);
  }
  .contact-list {
    position: absolute;
    left: 378px; top: 277px;
    list-style: none;
    font-size: 15.5px;
  }
  .contact-list li {
    display: flex; align-items: center;
    height: 26px;
  }
  .contact-list svg { width: 14px; height: 14px; margin-right: 12px; fill: var(--accent); }

  .address {
    position: absolute;
    left: 0; right: 0; top: 398px;
    text-align: center;
    font-size: 15.5px;
  }
</style>
</head>
<body>
  <section class="card card--front">
    <h1 class="brand-name">Pepper &amp; Palm</h1>
    <div class="mascot-art" role="img" aria-label="Cartoon illustration of a curry bowl and a naan walking together with hearts and sparkles"></div>
    <p class="tagline">“A match made in heaven”</p>
  </section>

  <section class="card card--back">
    <h2 class="brand-name">Pepper &amp; Palm</h2>

    <div class="owner">
      <p class="owner__name">Jaswinder Bains (Ravi)</p>
      <p class="owner__role">owner</p>
    </div>
    <div class="divider"></div>

    <ul class="contact-list">
      <li>
        <svg viewBox="0 0 16 16" aria-hidden="true"><path d="M2 6c0-2 2-3 6-3s6 1 6 3v1h-3V5.5H5V7H2zM4 8h8l1.5 5h-11z"/></svg>
        (480) 555-0147
      </li>
      <li>
        <svg viewBox="0 0 16 16" aria-hidden="true"><path d="M1 4h14v1L8 9 1 5zM1 6.5l7 4 7-4V12H1z"/></svg>
        RaviBains@postlark.com
      </li>
      <li>
        <svg viewBox="0 0 16 16" aria-hidden="true"><circle cx="8" cy="8" r="7"/></svg>
        www.PepperPalmLV.com
      </li>
    </ul>

    <p class="address">418 West Harmon Ave, #112 Henderson, NV 89052</p>
  </section>
</body>
</html>
```